Trading Company needs a business card design, letter head design and email signature

We need a double-sided business card design, letter head design and an email signature. We have a logo design.

Possible Tag Lines:
• “Connecting Worlds, Building Excellence.”
• “Global Sourcing, Local Excellence.”
• “Bridging Borders, Building Quality.”
• “Worldwide Partnerships, Superior Goods.”
• “Where Quality Meets Affordability”

Services Offered:
Procurement
Fabrication
Distribution
Logistics
Import/Export

Requirements
Must have
• Nice quality double sided Business Card design, Letterhead design needs to be A4
Nice to have
• possible ideas on tag lines

```html
<!DOCTYPE html>
<html lang="en">
<head>
<meta charset="utf-8">
<title>Tradevex Stationery</title>
<link rel="stylesheet" href="https://fonts.googleapis.com/css2?family=Arimo:wght@400;700&family=Questrial&display=swap">
<style>
:root{
  --bg:#9a999a;
  --paper:#ffffff;
  --red:#e8262c;
  --ink:#4d4f51;
  --text:#555759;
  --muted:#7a7c7e;
  --slate:#55585a;
  --rule:#6b6d6f;
  --faint-red:rgba(232,38,44,.06);
  --faint-grey:rgba(77,79,81,.06);
}
*{margin:0;padding:0;box-sizing:border-box}
html,body{width:1200px;height:930px;overflow:hidden;background:var(--bg);font-family:"Arimo",Arial,sans-serif;color:var(--text)}
.sheet{position:absolute;background:var(--paper);box-shadow:3px 4px 6px rgba(0,0,0,.35);overflow:hidden}
.brand{display:flex;align-items:center;gap:6px;font-family:"Arimo",Arial,sans-serif;font-weight:700;letter-spacing:.04em;color:var(--ink);position:absolute}
.brand .mark{background:var(--red);display:block}
.icon{width:1em;height:1em;vertical-align:-0.12em;margin-right:.45em;fill:none;stroke:var(--red);stroke-width:2}
.contact p{white-space:nowrap}
.faint-square{position:absolute;background:var(--faint-grey)}

/* letterhead */
.letterhead{left:49px;top:117px;width:492px;height:696px}
.letterhead .brand{left:42px;top:70px;font-size:22px}
.letterhead .brand .mark{width:18px;height:18px}
.letterhead .contact{position:absolute;left:358px;top:36px;font-size:7.8px;line-height:9.8px}
.letterhead .contact .gap{height:6px}
.letterhead .header-rule{position:absolute;left:42px;top:96px;width:408px;height:1px;background:var(--rule)}
.letterhead .greeting{position:absolute;left:45px;top:214px;font-family:"Questrial",sans-serif;font-size:11px;color:var(--ink);font-weight:700}
.letterhead .body{position:absolute;left:44px;top:247px;width:410px;font-size:8.1px;line-height:10.2px}
.letterhead .body p{margin-bottom:9px}
.letterhead .closing{position:absolute;left:45px;top:455px;font-size:6.5px;font-weight:700;color:var(--ink)}
.letterhead .signer{position:absolute;left:57px;top:488px;font-family:"Questrial",sans-serif;font-size:11.5px;color:var(--ink);letter-spacing:-.03em}
.letterhead .faint-square{left:290px;top:455px;width:200px;height:200px}

/* front card */
.card-front{left:573px;top:119px;width:343px;height:196px}
.card-front .brand{left:20px;top:82px;font-size:19px}
.card-front .brand .mark{width:15px;height:15px}
.card-front .divider{position:absolute;left:171px;top:49px;width:1px;height:97px;background:var(--rule)}
.card-front .details{position:absolute;left:183px;top:48px;font-size:9.4px;line-height:11.8px}
.card-front .name{color:var(--red);font-weight:700;font-size:12px;line-height:14px}
.card-front .role{color:var(--muted);margin-bottom:8px}
.card-front .gap{height:8px}

/* back card */
.card-back{left:573px;top:353px;width:343px;height:196px;background:var(--slate)}
.card-back .brand{left:15px;top:14px;font-size:20px;color:#fff}
.card-back .brand .mark{width:15px;height:15px}
.card-back .services{position:absolute;left:15px;top:80px;color:#fff;font-size:11px;line-height:13px}
.card-back .services h3{color:var(--red);font-size:10.5px;font-weight:400;text-transform:uppercase;margin-bottom:1px}
.card-back .services li{list-style:none}
.card-back .services li::before{content:"";display:inline-block;width:5px;height:5px;border:1.3px solid #fff;transform:rotate(45deg);margin:0 6px 1px 2px}
.card-back .tagline{position:absolute;left:15px;top:164px;color:#fff;font-size:11px}
.card-back .faint-square{left:190px;top:20px;width:150px;height:150px;background:rgba(255,255,255,.07)}

/* email signature */
.signature{left:573px;top:583px;width:578px;height:224px}
.signature .brand{left:53px;top:117px;font-size:31px}
.signature .brand .mark{width:24px;height:24px}
.signature .divider{position:absolute;left:286px;top:35px;width:2px;height:125px;background:var(--rule)}
.signature .details{position:absolute;left:306px;top:31px}
.signature .name{color:var(--red);font-weight:700;font-size:24px;line-height:26px}
.signature .role{color:var(--muted);font-size:19px;line-height:22px;margin-bottom:10px}
.signature .contact{font-size:19px;line-height:25px;color:var(--text)}
.signature .address{position:absolute;left:0;width:578px;top:183px;text-align:center;font-size:19px;color:var(--text)}
.signature .faint-square{left:400px;top:30px;width:160px;height:160px}
</style>
</head>
<body>
<svg width="0" height="0" style="position:absolute">
  <defs>
    <symbol id="i-phone" viewBox="0 0 24 24"><path d="M5 3h4l2 5-3 2a11 11 0 0 0 6 6l2-3 5 2v4a2 2 0 0 1-2 2A17 17 0 0 1 3 5a2 2 0 0 1 2-2z"/></symbol>
    <symbol id="i-mail" viewBox="0 0 24 24"><rect x="3" y="5" width="18" height="14" rx="1"/><path d="M3 6l9 7 9-7"/></symbol>
    <symbol id="i-web" viewBox="0 0 24 24"><circle cx="12" cy="12" r="9"/><path d="M3 12h18M12 3c3 3 3 15 0 18M12 3c-3 3-3 15 0 18"/></symbol>
  </defs>
</svg>

<section class="sheet letterhead">
  <div class="faint-square"></div>
  <div class="brand"><span class="mark"></span>TRADEVEX</div>
  <div class="contact">
    <p>Your Address, City</p>
    <p>State, Zip 0000</p>
    <div class="gap"></div>
    <p><svg class="icon"><use href="#i-phone"/></svg>123-456-2100</p>
    <p><svg class="icon"><use href="#i-mail"/></svg>youremail@example.com</p>
    <p><svg class="icon"><use href="#i-web"/></svg>www.yourwebsite.com</p>
  </div>
  <div class="header-rule"></div>
  <p class="greeting">Dear Mr. Reyes,</p>
  <div class="body">
    <p>Lorem ipsum dolor sit amet, consectetuer adipiscing elit, sed diam nonmmy nibh euismod tincidunt ut laor eet dolore magna aliquam erat volutpat. Ut wisi enim ad minim veniam, quis nostrud exerci tationmcorper suscipit lobortis nisl ut aliquip ex ea commodo consequat. Duis autem vel eum iriure dolor in hendrerit in vulputate velit esse molestie consequat, vel illum dolore eu feugiat</p>
    <p>Rorem ipsum dolor sit amet, consectetuer adipiscing elit, sed diam nonmmy nibh euismod tincidunt ut laor eet dolore magna aliquam erat volutpat. Ut wisi enim ad minim veniam, quis nostrud exerci tationmcorper suscipit lobortis nisl ut aliquip ex ea commodo consequat. Duis autem vel eum iriure dolor in hendrerit in vulputate velit esse molest</p>
    <p>Dorem ipsum dolor sit amet, consectetuer adipiscing elit, sed diam nonmmy nibh euismod tincidunt ut laor eet dolore magna aliquam erat volutpat. Ut wisi enim ad minim veniam, quis nostrud exerci tationmcorper suscipit lobortis nisl ut aliquip ex ea commodo consequat. Duis autem vel eum iriure dolor in hendrerit in suscipit lobortis nisl ut aliquip ex ea commodo consequat. Duis autem vel eum iriure dolor in hendrerit in vulputate velit esse molestie consequat, vel illum</p>
    <p>Sorem ipsum dolor sit amet, consectetuer adipiscing elit, sed diam nonmmy nibh euismod tincidunt ut laor eet dolore magna aliquam erat volutpat. Ut wisi enim ad minim veniam, quis nostrud exerci tationmcorper suscipit lobortis nisl ut aliquip ex ea commodo consequat. Duis autem vel eum iriure dolor in</p>
  </div>
  <p class="closing">Sincerely,</p>
  <p class="signer">Marcus Hale</p>
</section>

<section class="sheet card-front">
  <div class="brand"><span class="mark"></span>TRADEVEX</div>
  <div class="divider"></div>
  <div class="details contact">
    <p class="name">DANIEL REYES</p>
    <p class="role">Manager</p>
    <p>Your Address, City</p>
    <p>State, Zip 0000</p>
    <div class="gap"></div>
    <p><svg class="icon"><use href="#i-phone"/></svg>123-456-2100</p>
    <p><svg class="icon"><use href="#i-mail"/></svg>youremail@example.com</p>
    <p><svg class="icon"><use href="#i-web"/></svg>www.yourwebsite.com</p>
  </div>
</section>

<section class="sheet card-back">
  <div class="faint-square"></div>
  <div class="brand"><span class="mark"></span>TRADEVEX</div>
  <div class="services">
    <h3>Services Offered:</h3>
    <ul>
      <li>Procurement</li>
      <li>Fabrication</li>
      <li>Distribution</li>
      <li>Logistics</li>
      <li>Import/Export</li>
    </ul>
  </div>
  <p class="tagline">Connecting Worlds, Building Excellence</p>
</section>

<section class="sheet signature">
  <div class="faint-square"></div>
  <div class="brand"><span class="mark"></span>TRADEVEX</div>
  <div class="divider"></div>
  <div class="details">
    <p class="name">DANIEL REYES</p>
    <p class="role">Manager</p>
    <div class="contact">
      <p><svg class="icon"><use href="#i-phone"/></svg>123-456-2100</p>
      <p><svg class="icon"><use href="#i-mail"/></svg>youremail@example.com</p>
      <p><svg class="icon"><use href="#i-web"/></svg>www.yourwebsite.com</p>
    </div>
  </div>
  <p class="address">Your Address, City, State, Zip 0000</p>
</section>
</body>
</html>
```